****Business Card Design for Quarrystone Development. Design based around attached logo/company name

I’m looking for business card design for my company Quarrystone Development Group,LLC. Design should be professional, sharp and minimal. Outside of the attached logos, greyscale colors for remainder of cards. My thoughts are two-sided card with attached logo on one side and my info on the other but open to one-sided as well with right design.
Target Market(s)
Real estate professionals including banks, private investors, property owners, developers, commercial tenants like Brewlantern, Grovika or Tanquist’s.
Industry/Entity Type
Commercial real estate development and investments.
Contact Information for Business Card
Name, title, email, phone #’s, web address and physical address
Font styles to use
Other font styles liked:
- Helvetica, Garamond, etc
Colors
Designer to choose only greyscale colors for use in the design.
Requirements
Must have
- Attached logo first or second options.
Nice to have
- Two sided card with logo on one side. Attached Logo/company name can be laid out any way that flows as long as it’s legible.name
Should not have
- No loud colors. ***Please do not include logo, I have removed the company design with a logo image.

```html
<!DOCTYPE html>
<html lang="en">
<head>
<meta charset="UTF-8">
<title>Quarrystone Development Group, LLC — Business Card</title>
<link href="https://fonts.googleapis.com/css2?family=Cormorant+Garamond:wght@400&family=Arimo:wght@400&display=swap" rel="stylesheet">
<style>
  :root {
    --backdrop: #1f2023;
    --card: #4b5467;
    --card-edge: #434b5d;
    --ink: #eceef2;
    --ink-soft: #c9ced8;
    --rule: #d9dde4;
  }
  * { margin: 0; padding: 0; box-sizing: border-box; }
  html, body {
    width: 1200px;
    height: 900px;
    overflow: hidden;
    background: var(--backdrop);
  }
  .canvas {
    position: relative;
    width: 1200px;
    height: 900px;
  }
  .card {
    position: absolute;
    left: 250px;
    width: 700px;
    height: 400px;
    background: var(--card);
    border: 1px solid var(--card-edge);
    box-shadow: 0 10px 28px rgba(0, 0, 0, 0.45);
  }
  .card--front { top: 30px; }
  .card--back { top: 470px; }

  .company {
    position: absolute;
    left: 0;
    right: 0;
    top: 140px;
    display: flex;
    flex-direction: column;
    align-items: center;
    font-family: "Arimo", Helvetica, Arial, sans-serif;
    font-weight: 400;
    color: var(--ink);
  }
  .company__name {
    font-size: 46px;
    line-height: 1;
    letter-spacing: 2px;
  }
  .company__rule {
    width: 380px;
    height: 1px;
    margin-top: 10px;
    background: var(--rule);
  }
  .company__group {
    margin-top: 10px;
    font-size: 17px;
    line-height: 1;
    letter-spacing: 3px;
    font-weight: 400;
  }

  .details {
    position: absolute;
    left: 0;
    top: 208px;
    width: 700px;
    height: 130px;
  }
  .identity {
    position: absolute;
    right: 362px;
    top: 0;
    text-align: right;
    color: var(--ink);
  }
  .identity__name {
    font-family: "Cormorant Garamond", Garamond, serif;
    font-size: 30px;
    letter-spacing: 1px;
    line-height: 1;
    text-transform: uppercase;
  }
  .identity__title,
  .identity__address {
    font-family: "Arimo", Helvetica, Arial, sans-serif;
    font-size: 15px;
    line-height: 20px;
    color: var(--ink-soft);
  }
  .identity__title { margin-top: 4px; }
  .divider {
    position: absolute;
    left: 352px;
    top: 6px;
    width: 1px;
    height: 96px;
    background: var(--rule);
  }
  .contacts {
    position: absolute;
    left: 366px;
    top: 8px;
    list-style: none;
    font-family: "Arimo", Helvetica, Arial, sans-serif;
    font-size: 16px;
    line-height: 24px;
    color: var(--ink);
  }
  .contacts li {
    display: flex;
    align-items: center;
    gap: 9px;
  }
  .contacts svg {
    width: 13px;
    height: 13px;
    fill: var(--ink);
    flex: none;
  }
</style>
</head>
<body>
<main class="canvas">
  <section class="card card--front" aria-label="Card front">
    <h1 class="company">
      <span class="company__name">Quarrystone</span>
      <span class="company__rule" aria-hidden="true"></span>
      <span class="company__group">Development Group, LLC</span>
    </h1>
  </section>

  <section class="card card--back" aria-label="Card back">
    <div class="details">
      <div class="identity">
        <p class="identity__name">Daniel Ashford</p>
        <p class="identity__title">President</p>
        <p class="identity__address">4120 Harlow Ridge Road<br>Fairmont, Oregon 97418</p>
      </div>
      <div class="divider"></div>
      <ul class="contacts">
        <li>
          <svg viewBox="0 0 16 16" aria-hidden="true"><path d="M3.2 1.2l2.4 2.9-1.3 1.6c.9 2 2.6 3.7 4.6 4.6l1.6-1.3 2.9 2.4-1.4 2.6C6.7 13.6 2.4 9.3 .6 3.9z"/></svg>
          <span>555-214-0386</span>
        </li>
        <li>
          <svg viewBox="0 0 16 16" aria-hidden="true"><path d="M4 1h8v4H4zM1 6h14v6h-3v3H4v-3H1zm4 4v3h6v-3z"/></svg>
          <span>555-327-0519</span>
        </li>
        <li>
          <svg viewBox="0 0 16 16" aria-hidden="true"><path d="M1 3h14v1.2L8 9 1 4.2zM1 5.8l7 4.7 7-4.7V13H1z"/></svg>
          <span>name@quarrystone.com</span>
        </li>
        <li>
          <svg viewBox="0 0 16 16" aria-hidden="true"><path d="M8 1a7 7 0 100 14A7 7 0 008 1zm-1 2.2c-.6 1-1 2-.5 2.8.6.9 2 .4 2.3 1.5.3 1-1 1.6-.6 2.8.3.9 1.3 1.5 1.1 2.5A5 5 0 013.2 6.4c1 .2 2-.5 2.4-1.5.2-.6.6-1.2 1.4-1.7z"/></svg>
          <span>www.quarrystone.com</span>
        </li>
      </ul>
    </div>
  </section>
</main>
</body>
</html>
```